Otter Bites Guild - A Monthly Subscription Dog Treats Club - Shopify Website Design

A monthly subscription company. Need a Shopify Website Design and uploaded to fully work with Crisp Renewals.

Please look at these sites for examples as well as the images I enclosed.

https://www.mealbrightly.com/
https://www.globalmunchbox.com/

Number of Pages Required

1 page

```html
<!DOCTYPE html>
<html lang="en">
<head>
<meta charset="utf-8">
<title>Otter Bites Guild – Monthly Dog Treats Club</title>
<link href="https://fonts.googleapis.com/css2?family=Lora:wght@400;700&family=Mulish:wght@400;600;700&display=swap" rel="stylesheet">
<style>
:root{
  --green:#2f4a3c;
  --ink:#222;
  --muted:#555;
  --faint:#aaa;
  --line:#e6e6e6;
  --white:#fff;
  --panel:#ececec;
}
*{box-sizing:border-box;margin:0;padding:0}
html,body{width:1200px;height:3694px;overflow:hidden}
body{position:relative;background:var(--white);color:var(--ink);font-family:'Mulish',sans-serif}
.abs{position:absolute}
.serif{font-family:'Lora',serif}
.center{left:0;width:1200px;text-align:center}
.promo-bar{top:0;left:0;width:1200px;height:47px;background:var(--green);color:var(--white);font-size:14px;line-height:47px;text-align:center}
.hero{top:47px;left:0;width:1200px;height:501px;background:linear-gradient(120deg,#2b2420 0%,#4a3a30 45%,#6b5646 70%,#3a2e26 100%)}
.hero-shade{inset:0;background:rgba(0,0,0,.35)}
.brand{font-size:24px;color:var(--white);font-weight:400}
.nav{top:88px;left:598px;display:flex;gap:0;font-size:12.5px;font-weight:700;color:var(--white);letter-spacing:.3px}
.nav span{position:absolute;white-space:nowrap}
.nav-rule{top:143px;left:110px;width:980px;height:1px;background:rgba(255,255,255,.35)}
.hero-title{top:193px;font-size:35px;color:var(--white)}
.hero-text{top:250px;left:220px;width:760px;text-align:center;font-family:'Lora',serif;font-size:15px;line-height:26px;color:var(--white)}
.btn{display:block;border-radius:26px;text-align:center;font-size:13px;letter-spacing:.3px}
.btn-light{top:344px;left:508px;width:185px;height:46px;line-height:46px;background:#f2f2f2;color:#333}
.dots{top:506px;left:577px;display:flex;gap:6px}
.dots i{width:11px;height:11px;border-radius:50%;border:1.5px solid var(--white);display:block}
.dots i.on{background:var(--white)}
.sec-title{font-family:'Lora',serif;font-size:32px;color:var(--ink)}
.sec-sub{font-size:13px;color:var(--ink)}
.step{width:300px;text-align:center}
.step h3{font-family:'Lora',serif;font-weight:400;font-size:24px;margin:18px 0 16px}
.step p{font-size:13px;line-height:16px;color:var(--ink)}
.rule{left:0;width:1200px;height:1px;background:var(--line)}
.feature-img{top:1011px;left:609px;width:591px;height:455px;background:radial-gradient(circle at 35% 55%,#c49a66 0,#b68a58 22%,#e2e2e2 48%,#ececec 100%)}
.pager{top:1130px;left:142px;display:flex;gap:6px}
.pager span{width:46px;height:46px;border-radius:50%;border:1.5px solid var(--green);color:var(--green);font-size:12px;line-height:43px;text-align:center}
.pager span.on{background:var(--green);color:var(--white)}
.feature-title{top:1194px;left:143px;font-family:'Lora',serif;font-weight:700;font-size:24px;color:var(--green)}
.feature-text{top:1248px;left:146px;width:400px;font-size:13px;line-height:16.5px;color:var(--green)}
.product{height:202px}
.btn-outline{border:1px solid #cfcfcf;background:var(--white);color:#333;height:49px;line-height:47px;width:189px;left:506px}
.quote{font-size:11px;line-height:21px;text-align:center;width:380px}
.avatar{width:58px;height:58px;border-radius:50%;background:#d9d2cc}
.person b{display:block;font-size:14px;font-weight:600}
.person small{font-size:9px}
.faded{color:var(--faint)}
.news-img{top:2534px;width:484px;height:308px}
.news-col{top:2860px;width:484px;text-align:center}
.news-col h3{font-family:'Lora',serif;font-weight:400;font-size:25px}
.news-col .date{font-size:13px;margin-top:10px}
.news-col p{font-size:15px;line-height:26px;margin-top:14px;color:#333}
.newsletter{top:3118px;left:0;width:1200px;height:271px;background:var(--green);color:var(--white)}
.field{top:162px;left:371px;width:431px;height:48px;background:var(--white);color:#333;font-size:13px;line-height:48px;padding-left:15px}
.field-btn{top:162px;left:747px;width:55px;height:48px;background:#b6b6b6}
.foot-head{top:3432px;font-family:'Lora',serif;font-weight:700;font-size:14px;letter-spacing:.5px;color:var(--ink)}
.foot-links{font-size:13px;font-weight:600;line-height:25.5px;color:var(--ink)}
.foot-about{top:3475px;left:777px;width:340px;font-size:13px;font-weight:600;line-height:25.5px}
.legal{top:3642px;left:119px;font-size:13px;font-weight:600}
.currency{top:3645px;left:985px;font-size:13px;font-weight:600}
</style>
</head>
<body>

<div class="abs promo-bar">Subscribe to our newsletter and receive 15% off of your first online order!</div>

<section class="abs hero" role="img" aria-label="Photo of hands opening a treat jar beside a dog"></section>
<div class="abs brand" style="top:80px;left:110px">Otter Bites Guild.</div>
<nav class="abs nav">
  <span style="left:0">SHOP</span>
  <span style="left:64px">SUBSCRIPTION</span>
  <span style="left:187px">ABOUT US &nbsp;⌄</span>
  <span style="left:315px">CONTACT</span>
</nav>
<svg class="abs" style="top:87px;left:1061px" width="18" height="18" viewBox="0 0 24 24" fill="none" stroke="#fff" stroke-width="1.8"><path d="M2 3h3l3 12h11l2-8H6"/><circle cx="9" cy="20" r="1.5"/><circle cx="18" cy="20" r="1.5"/></svg>
<div class="abs nav-rule"></div>
<h1 class="abs center hero-title serif" style="font-weight:400">Monthly Subscription of Dog Treats Club.</h1>
<p class="abs hero-text">Lorem ipsum dolor sit amet, consectetur adipiscing elit, sed do eiusmod tempor incididunt ut labore et dolore magna aliqua. Ut enim ad minim veniam, quis nostrud exercitation ullamco laboris nisi</p>
<a class="abs btn btn-light">LEARN MORE</a>
<div class="abs dots"><i class="on"></i><i></i><i></i></div>

<h2 class="abs center sec-title" style="top:626px;font-weight:400">How it Works</h2>
<p class="abs center sec-sub" style="top:670px">Sed ut perspiciatis unde omnis iste natus error</p>

<div class="abs step" style="top:750px;left:114px">
  <svg width="40" height="40" viewBox="0 0 40 40" fill="none" stroke="#222" stroke-width="1.8"><ellipse cx="9" cy="17" rx="3.5" ry="4.5"/><ellipse cx="16" cy="9" rx="3.5" ry="4.5"/><ellipse cx="24" cy="9" rx="3.5" ry="4.5"/><ellipse cx="31" cy="17" rx="3.5" ry="4.5"/><path d="M20 20c-6 0-11 8-9 12 2 3 6 1 9 1s7 2 9-1c2-4-3-12-9-12z"/></svg>
  <h3>Step 1</h3>
  <p>Sed ut perspiciatis unde omnis iste natus error sit voluptatem accusantium doloremque laudantiuma</p>
</div>
<div class="abs step" style="top:750px;left:450px">
  <svg width="40" height="40" viewBox="0 0 40 40" fill="none" stroke="#222" stroke-width="1.8"><rect x="5" y="14" width="30" height="7"/><rect x="7" y="21" width="26" height="16"/><path d="M17 14v23M23 14v23M20 14c-4-8-12-6-8-1M20 14c4-8 12-6 8-1"/></svg>
  <h3>Step 2</h3>
  <p>Sed ut perspiciatis unde omnis iste natus error sit voluptatem accusantium doloremque laudantiuma</p>
</div>
<div class="abs step" style="top:750px;left:785px">
  <svg width="40" height="40" viewBox="0 0 40 40" fill="none" stroke="#222" stroke-width="1.8"><path d="M4 7h5l4 19h18l4-14H11"/><circle cx="15" cy="33" r="2.5"/><circle cx="28" cy="33" r="2.5"/></svg>
  <h3>Step 3</h3>
  <p>Sed ut perspiciatis unde omnis iste natus error sit voluptatem accusantium doloremque laudantiuma</p>
</div>

<div class="abs rule" style="top:1011px"></div>
<div class="abs feature-img" role="img" aria-label="Photo of a small dog beside a food bowl and cans of dog food"></div>
<div class="abs pager"><span class="on">1</span><span>2</span><span>3</span></div>
<h3 class="abs feature-title">Finibus Bonorum et</h3>
<p class="abs feature-text">Sed ut perspiciatis unde omnis iste natus error sit voluptatem accusantium doloremque laudantium, totam rem aperiam, eaque ipsa quae ab illo inventore veritatis et quasi architecto beatae vitae dicta sunt explicabo.</p>
<div class="abs rule" style="top:1466px"></div>

<h2 class="abs center sec-title" style="top:1544px;font-weight:400">Best Products</h2>
<p class="abs center sec-sub" style="top:1595px">What our customers are loving lately.</p>
<div class="abs product" style="top:1646px;left:110px;width:309px;background:linear-gradient(135deg,#a9cfd0,#e5c9a0)" role="img" aria-label="Photo of decorated dog cookies in a box"></div>
<div class="abs product" style="top:1646px;left:473px;width:208px;background:linear-gradient(135deg,#fff,#e9a2a0 45%,#8cc27a 75%,#fff)" role="img" aria-label="Photo of bone-shaped dog treats in a gift box"></div>
<div class="abs product" style="top:1646px;left:827px;width:248px;background:linear-gradient(135deg,#fff,#e98bb0 35%,#56b5e8 65%,#fff)" role="img" aria-label="Photo of pink and blue feeding bowls with kibble"></div>
<a class="abs btn btn-outline" style="top:1874px">SHOP ALL</a>
<div class="abs rule" style="top:1970px"></div>

<h2 class="abs center sec-title" style="top:2026px;font-weight:400">Testimonials</h2>
<p class="abs center sec-sub" style="top:2077px">Hear what our customers have to say about us</p>

<p class="abs quote faded" style="top:2152px;left:-30px">Sed ut perspiciatis unde omnis iste natus error sit voluptatem accusantium doloremque laudantium, totam rem aperiam, eaque ipsa quae.</p>
<p class="abs quote" style="top:2152px;left:410px">Sed ut perspiciatis unde omnis iste natus error sit voluptatem accusantium doloremque laudantium, totam rem aperiam, eaque ipsa quae.</p>
<p class="abs quote faded" style="top:2152px;left:865px">Sed ut perspiciatis unde omnis iste natus error sit voluptatem accusantium doloremque laudantium, totam rem aperiam, eaque ipsa quae.</p>

<div class="abs avatar" style="top:2216px;left:46px;opacity:.45" role="img" aria-label="Customer portrait"></div>
<div class="abs person faded" style="top:2226px;left:131px"><b>Joe</b><small>Loriumipsum</small></div>
<div class="abs avatar" style="top:2216px;left:491px;background:#6d5a4c" role="img" aria-label="Customer portrait"></div>
<div class="abs person" style="top:2226px;left:576px"><b>Jennifer</b><small>Loriumipsum</small></div>
<div class="abs avatar" style="top:2216px;left:974px;opacity:.45" role="img" aria-label="Customer portrait"></div>
<div class="abs person faded" style="top:2220px;left:1059px"><b>John</b><small>Loriumipsum</small></div>
<svg class="abs" style="top:2238px;left:354px" width="24" height="14" viewBox="0 0 24 14" fill="none" stroke="#333" stroke-width="1.5"><path d="M23 7H2M8 1 2 7l6 6"/></svg>
<svg class="abs" style="top:2232px;left:823px" width="24" height="14" viewBox="0 0 24 14" fill="none" stroke="#333" stroke-width="1.5"><path d="M1 7h21M16 1l6 6-6 6"/></svg>
<div class="abs rule" style="top:2383px"></div>

<h2 class="abs center sec-title" style="top:2419px;font-weight:400">Latest News</h2>
<p class="abs center sec-sub" style="top:2473px">Check out our blog for what we've been doing and thinking about lately.</p>
<div class="abs news-img" style="left:105px;background:linear-gradient(120deg,#e4b24a,#a8953e 50%,#4d6e8f)" role="img" aria-label="Photo of a man hugging a golden dog in a field"></div>
<div class="abs news-img" style="left:612px;background:linear-gradient(120deg,#b2363a,#6d4a3e 45%,#efe6da 75%,#8a4a2c)" role="img" aria-label="Photo of a man feeding a white dog"></div>
<div class="abs news-col" style="left:105px">
  <h3>Excepteur sint occaecat cupidatat</h3>
  <div class="date">APR 28, 2019</div>
  <p>Lorem ipsum dolor sit amet, consectetur adipiscing elit, sed do eiusmod tempor incididunt ut labore et dolore</p>
</div>
<div class="abs news-col" style="left:612px">
  <h3>Excepteur sint occaecat cupidatat</h3>
  <div class="date">APR 28, 2019</div>
  <p>Lorem ipsum dolor sit amet, consectetur adipiscing elit, sed do eiusmod tempor incididunt ut labore et dolore</p>
</div>
<a class="abs btn btn-outline" style="top:3027px">SEE ALL</a>

<section class="abs newsletter">
  <h2 class="abs center serif" style="top:41px;font-weight:400;font-size:32px">Newsletter</h2>
  <p class="abs center" style="top:100px;font-size:16px">Sign up to receive 15% off of your first online order.</p>
  <div class="abs field">Email Address</div>
  <div class="abs field-btn"><svg style="margin:17px 0 0 18px" width="18" height="14" viewBox="0 0 24 14" fill="none" stroke="#444" stroke-width="1.5"><path d="M1 7h21M16 1l6 6-6 6"/></svg></div>
</section>

<div class="abs" style="top:3480px;left:112px;font-size:24px">Otter Bites Guild.</div>
<div class="abs foot-head" style="left:434px">NAVIGATE</div>
<div class="abs foot-head" style="left:598px">NEED HELP</div>
<div class="abs foot-head" style="left:777px">ABOUT THE CONTENT</div>
<div class="abs foot-links" style="top:3470px;left:436px">Shop<br>Subscription<br>About Us<br>Contact</div>
<div class="abs foot-links" style="top:3470px;left:600px">Q&amp;A<br>Shipping &amp; Returns<br>Wholesale<br>Contact</div>
<p class="abs foot-about">Sed ut perspiciatis unde omnis iste natus error sit voluptatem accusantium doloremque laudantium, totam rem aperiam,</p>
<div class="abs legal">© 2020 &nbsp;| &nbsp;www.companyname.com</div>
<div class="abs currency">USD $ &nbsp;&nbsp;⌄</div>

</body>
</html>
```